New Business Card Design for Manufacturing

We are an engineering/manufacturing company that offers Advanced machining/assembly/engineering services, as well as innovative products for the heavy duty engine cooling markets.

We are looking to get a new business card designed that is clean and modern looking, but still fits the wide range of technical/skilled work we do.

- We hope to use this design as the base for other design work in new Presentations, web, and print work.

Industry/Entity Type

Engineering

Contact Information for Business Card

Our preferred color of blue is (RGB) 22/71/159 but can vary slightly from that color. Our content will be our Logo and full company name (Vantrell Forge Works, Inc.), company address, name, job title, phone number with extension, cell number, fax number, website, and email address on the cards.
We'd like the full company name next to the logo, but we are open to other interpretations of that layout.
Preferably, we would like the back side to be clean with just our logo, and the front to contain all of the contact information.

Colors
2f74b4
0355a3
85abd2

Requirements
Must have
• - Logo, company name, needed content - We are open to interpretation beyond that.
• - Standard size business card.
• - Horizontal orientation.
• - Enough space for lengthy names / job titles (for example, a job title could read "Directory of Human Resources" or "V.P. of Governmental Affairs"). We need this to look clean, whether the title be short (CEO) or long (as described above).

```html
<!DOCTYPE html>
<html lang="en">
<head>
<meta charset="utf-8">
<title>Vantrell Forge Works – Business Card</title>
<link href="https://fonts.googleapis.com/css2?family=Open+Sans:wght@400;600;700;800&display=swap" rel="stylesheet">
<style>
  :root {
    --backdrop: #4a4a4c;
    --card: #1f1f21;
    --card-edge: #29292b;
    --gloss: #3c3c3f;
    --ghost: #28282a;
    --brand-blue: #1d6fc2;
    --text-light: #f2f2f2;
    --text-soft: #d8d8d8;
  }
  * { box-sizing: border-box; margin: 0; padding: 0; }
  html, body { width: 799px; height: 1200px; overflow: hidden; }
  body {
    background: var(--backdrop);
    font-family: "Open Sans", Arial, sans-serif;
    position: relative;
  }
  .card {
    position: absolute;
    left: 110px;
    width: 580px;
    height: 332px;
    background: var(--card);
    border: 1px solid var(--card-edge);
    overflow: hidden;
  }
  .card--front { top: 134px; }
  .card--back { top: 734px; }

  /* Front: wordmark */
  .wordmark {
    position: absolute;
    inset: 0;
    display: flex;
    align-items: center;
    justify-content: center;
    gap: 16px;
  }
  .wordmark__square {
    width: 34px; height: 34px;
    background: var(--gloss);
  }
  .wordmark__name {
    font-weight: 800;
    font-size: 38px;
    letter-spacing: 0.5px;
    color: var(--gloss);
  }

  /* Back: faint name decoration */
  .ghost-name {
    position: absolute;
    left: 60px;
    top: 92px;
    font-weight: 800;
    font-size: 118px;
    line-height: 1;
    color: var(--ghost);
    letter-spacing: 2px;
    white-space: nowrap;
  }

  .identity {
    position: absolute;
    right: 318px;
    top: 62px;
    text-align: right;
  }
  .identity__name {
    color: var(--brand-blue);
    font-weight: 600;
    font-size: 25px;
    line-height: 1.2;
    margin-bottom: 4px;
  }
  .identity__role {
    color: var(--text-soft);
    font-size: 12.5px;
    line-height: 1.45;
  }

  .divider-vertical {
    position: absolute;
    left: 282px;
    top: 58px;
    width: 1.5px;
    height: 150px;
    background: var(--brand-blue);
  }
  .divider-horizontal {
    position: absolute;
    left: 0;
    right: 0;
    top: 226px;
    height: 1.5px;
    background: var(--brand-blue);
  }

  .contact {
    position: absolute;
    left: 300px;
    top: 66px;
    list-style: none;
  }
  .contact__item {
    display: flex;
    align-items: center;
    gap: 9px;
    color: var(--text-light);
    font-size: 13.5px;
    line-height: 20px;
  }
  .contact__icon { width: 12px; height: 12px; flex: none; }
  .contact__accent { color: var(--brand-blue); }
  .contact__address {
    color: var(--text-light);
    font-size: 13.5px;
    line-height: 19px;
    padding-left: 0;
    margin-top: 2px;
  }

  .company-name {
    position: absolute;
    left: 36px;
    top: 248px;
    color: var(--text-light);
    font-weight: 700;
    font-size: 21px;
    letter-spacing: 0.3px;
  }
</style>
</head>
<body>

  <section class="card card--front" aria-label="Card back side">
    <div class="wordmark">
      <span class="wordmark__square"></span>
      <span class="wordmark__name">Vantrell Forge Works</span>
    </div>
  </section>

  <section class="card card--back" aria-label="Card contact side">
    <div class="ghost-name" aria-hidden="true">VANTRELL</div>

    <div class="identity">
      <p class="identity__name">Marlow Keene Ashby</p>
      <p class="identity__role">Managing Director / Admin<br>PHd Holder / Owner /<br>Technician / Developer / Producer</p>
    </div>

    <div class="divider-vertical"></div>

    <ul class="contact">
      <li class="contact__item">
        <svg class="contact__icon" viewBox="0 0 12 12"><path fill="#1d6fc2" d="M2.5 1h2l1 2.6-1.3 1a6 6 0 0 0 3.2 3.2l1-1.3 2.6 1v2a1 1 0 0 1-1 1A9.5 9.5 0 0 1 1.5 2a1 1 0 0 1 1-1z"/></svg>
        555-0142-2200 (VFW)
      </li>
      <li class="contact__item">
        <svg class="contact__icon" viewBox="0 0 12 12"><rect x="3" y="0.5" width="6" height="11" rx="1" fill="#1d6fc2"/><rect x="4" y="2" width="4" height="7" fill="#1f1f21"/></svg>
        555-0188-3310
      </li>
      <li class="contact__item">
        <svg class="contact__icon" viewBox="0 0 12 12"><rect x="3" y="0.5" width="6" height="3.5" fill="#1d6fc2"/><rect x="0.5" y="4.5" width="11" height="5" rx="1" fill="#1d6fc2"/><rect x="3" y="8" width="6" height="3.5" fill="#1d6fc2" stroke="#1f1f21" stroke-width="0.8"/></svg>
        555-0173-4420
      </li>
      <li class="contact__item">
        <svg class="contact__icon" viewBox="0 0 12 12"><rect x="0.5" y="2" width="11" height="8" fill="#1d6fc2"/><path d="M0.5 2 6 6.5 11.5 2" fill="none" stroke="#1f1f21" stroke-width="1"/></svg>
        mashby@vantrellforge.com
      </li>
      <li class="contact__item">
        <svg class="contact__icon" viewBox="0 0 12 12"><circle cx="6" cy="6" r="5.5" fill="#1d6fc2"/><path d="M0.5 6h11M6 0.5c-2.5 3-2.5 8 0 11M6 0.5c2.5 3 2.5 8 0 11" fill="none" stroke="#1f1f21" stroke-width="0.8"/></svg>
        <span>www.<span class="contact__accent">vantrellforge</span>.com</span>
      </li>
      <li class="contact__address">718 Foundry Row, Millbrook,<br>Cedar Falls, US 504321</li>
    </ul>

    <div class="divider-horizontal"></div>

    <p class="company-name">Vantrell Forge Works, Inc.</p>
  </section>

</body>
</html>
```